Business Card Design Project

Business Card
We are rebranding with a new logo
Industry/Entity Type
Business
Contact Information for Business Card
Dennis Morvale +61 487215963 dennis@quorv.com.au P.O. Box 872 Fernlow QLD 4309
Requirements
Must have
- Logo

```html
<!DOCTYPE html>
<html lang="en">
<head>
<meta charset="utf-8">
<title>Quorv International – Business Card</title>
<link rel="stylesheet" href="https://fonts.googleapis.com/css2?family=Roboto:wght@400;500&family=Roboto+Condensed:wght@700&display=swap">
<style>
  :root {
    --backdrop: #262626;
    --card: #f2f2f2;
    --blue: #0a8ac4;
    --blue-deep: #0b5a80;
    --navy: #0a3550;
    --orange: #e8791f;
    --text: #4a4a4a;
    --white: #ffffff;
  }
  html, body {
    margin: 0;
    width: 1200px;
    height: 960px;
    overflow: hidden;
    background: var(--backdrop);
  }
  .card {
    position: absolute;
    left: 223px;
    top: 265px;
    width: 754px;
    height: 430px;
    border-radius: 22px;
    overflow: hidden;
    background: var(--card);
  }
  .card-art {
    position: absolute;
    inset: 0;
    display: block;
  }
  .holder-name {
    position: absolute;
    left: 42px;
    top: 32px;
    margin: 0;
    font: 700 27px/1 "Roboto Condensed", sans-serif;
    color: var(--white);
    letter-spacing: 0.2px;
  }
  .brand {
    position: absolute;
    right: 48px;
    top: 250px;
    display: flex;
    align-items: center;
    gap: 12px;
    font: 500 27px/1 "Roboto", sans-serif;
    letter-spacing: 2px;
    color: var(--blue-deep);
    text-transform: uppercase;
  }
  .brand-dot {
    width: 22px;
    height: 22px;
    border-radius: 50%;
    background: var(--orange);
  }
  .contact-list {
    position: absolute;
    left: 44px;
    top: 319px;
    margin: 0;
    padding: 0;
    list-style: none;
    font: 400 18px/23.5px "Roboto", sans-serif;
    color: var(--text);
  }
  .contact-list li {
    display: flex;
    align-items: center;
    gap: 10px;
  }
  .contact-icon {
    width: 18px;
    height: 18px;
    flex: none;
    fill: var(--blue);
  }
  .postal-address {
    position: absolute;
    right: 44px;
    top: 344px;
    margin: 0;
    font: 400 18px/23.5px "Roboto", sans-serif;
    font-style: normal;
    text-align: right;
    color: var(--text);
  }
</style>
</head>
<body>
  <article class="card">
    <svg class="card-art" viewBox="0 0 754 430" aria-hidden="true">
      <defs>
        <radialGradient id="band-glow" cx="0.5" cy="0.1" r="0.7">
          <stop offset="0" stop-color="#16a6e0"/>
          <stop offset="0.55" stop-color="var(--blue)"/>
          <stop offset="1" stop-color="var(--blue-deep)"/>
        </radialGradient>
      </defs>
      <path d="M0 0 H754 V90 C520 70 240 110 0 200 Z" fill="url(#band-glow)"/>
      <path d="M0 200 C240 110 520 70 754 90 V86 C520 66 240 104 0 188 Z" fill="var(--navy)"/>
      <path d="M14 194 C250 112 500 82 700 86 C500 86 260 118 14 194 Z" fill="var(--orange)"/>
    </svg>

    <h1 class="holder-name">DENNIS MORVALE</h1>

    <div class="brand">
      <span class="brand-dot"></span>
      <span class="brand-name">Quorv International</span>
    </div>

    <ul class="contact-list">
      <li>
        <svg class="contact-icon" viewBox="0 0 24 24"><path d="M6.6 10.8a15 15 0 0 0 6.6 6.6l2.2-2.2c.3-.3.7-.4 1-.2 1.1.4 2.3.6 3.6.6.6 0 1 .4 1 1V20c0 .6-.4 1-1 1A17 17 0 0 1 3 4c0-.6.4-1 1-1h3.5c.6 0 1 .4 1 1 0 1.3.2 2.5.6 3.6.1.3 0 .7-.2 1z"/></svg>
        <span>+61 487215963</span>
      </li>
      <li>
        <svg class="contact-icon" viewBox="0 0 24 24"><path d="M3 6h18v12H3z M3 6l9 7 9-7" stroke="var(--card)" stroke-width="1.5"/></svg>
        <span>dennis@quorv.com.au</span>
      </li>
      <li>
        <svg class="contact-icon" viewBox="0 0 24 24"><circle cx="12" cy="12" r="9"/></svg>
        <span>www.quorv.com.au</span>
      </li>
    </ul>

    <address class="postal-address">
      P.O. Box 872<br>
      Fernlow QLD 4309
    </address>
  </article>
</body>
</html>
```